Best local air conditioning and heating contractor

We need a website design for a new company in Tampa Bay called the Coastal Breeze Cooling Company. We provide superior services for residential and commercial properties as well as maintenance and installing HVAC systems. We also want to sell equipment, parts and filter on the website as well. We want it easy to use for customers. Rich with content and keywords for our area.

Target Market(s)

homeowners in Tampa Bay

Industry/Entity Type

HVAC air conditioning and heating

Coding

Coded - Design and coding required

Number of Pages Required

5+ page

Font styles to use
Sans Serif

Requirements
Nice to have
• would like the colors to be same as logo

```html
<!DOCTYPE html>
<html lang="en">
<head>
<meta charset="utf-8">
<title>Coastal Breeze Cooling Company — Heating and Air Conditioning</title>
<link href="https://fonts.googleapis.com/css2?family=Poppins:wght@300;400;500;600;700&display=swap" rel="stylesheet">
<style>
:root{
  --red:#d7222a;
  --blue:#1f4b8f;
  --navy:#12326b;
  --ink:#0e1630;
  --dark:#222;
  --grey:#f0f0f0;
  --text:#555;
  --white:#fff;
}
*{box-sizing:border-box;margin:0;padding:0}
html,body{width:1200px;height:4205px;overflow:hidden}
body{position:relative;font-family:'Poppins',sans-serif;color:var(--dark);background:var(--white)}
.abs{position:absolute}

/* header */
.topbar{left:534px;top:0;width:666px;height:44px;background:var(--navy);display:flex;align-items:center;color:#fff;font-size:14px}
.topbar .item{display:flex;align-items:center;gap:12px;margin-left:40px}
.topbar .dot{width:20px;height:20px;border-radius:50%;background:var(--red);display:flex;align-items:center;justify-content:center}
.topbar .social{margin-left:auto;margin-right:40px;display:flex;gap:10px}
.topbar .social span{width:13px;height:13px;border-radius:50%;background:#fff;display:block}
.logo{left:29px;top:30px;display:flex;align-items:center;gap:10px}
.logo .mark{width:34px;height:34px;border-radius:50%;background:var(--red)}
.logo .name{font-weight:700;color:var(--navy);font-size:17px;line-height:1.15;text-transform:uppercase}
.nav{top:68px;left:317px;font-size:17px;font-weight:500;color:#222}
.nav a{position:absolute;white-space:nowrap;color:inherit;text-decoration:none}
.btn{background:var(--red);color:#fff;display:flex;align-items:center;justify-content:center;font-weight:500;text-transform:uppercase}
.quote-top{left:988px;top:54px;width:171px;height:44px;font-size:17px}

/* hero */
.hero-bg{left:0;top:114px}
.hero-title{left:0;top:245px;width:1163px;text-align:center;color:#fff;font-size:54px;font-weight:600;line-height:65px;text-transform:uppercase}
.hero-sub{left:0;top:463px;width:1163px;text-align:center;color:#e4e4e4;font-size:20px;font-weight:300;line-height:24px}
.hero-btn{left:482px;top:573px;width:232px;height:57px;font-size:23px}

.feature{width:222px;height:189px;background:#fff;border-radius:8px;box-shadow:0 3px 12px rgba(0,0,0,.12);top:735px;text-align:center}
.feature svg{margin-top:20px}
.feature h3{font-size:15px;font-weight:500;margin-top:6px}
.feature p{font-size:8px;color:#777;line-height:15px;margin-top:10px;text-transform:uppercase}
.feature .more{font-size:11px;color:var(--red);font-weight:600;margin-top:14px}

/* about */
.about-photo{left:100px;top:1047px;width:374px;height:299px;border-radius:6px;background:linear-gradient(135deg,#5b4a3c,#8a7360 40%,#3b5a8f 75%,#2a2f3a)}
.badge{left:392px;top:1225px;width:156px;height:156px;border-radius:50%;background:var(--navy);color:#fff;text-align:center}
.badge b{display:block;font-size:58px;font-weight:600;line-height:58px;margin-top:38px}
.badge span{font-size:12px;font-weight:500}
.about-h{left:583px;top:1078px;font-size:26px;font-weight:600}
.about-p{left:586px;top:1130px;width:420px;font-size:14px;font-weight:300;color:#666;line-height:17px}
.about-p p+p{margin-top:8px}
.about-btn{left:586px;top:1306px;width:165px;height:41px;font-size:14px;text-transform:none}

/* services */
.section-h{left:0;width:1166px;text-align:center;font-size:26px;font-weight:600;text-transform:uppercase}
.svc{width:263px;height:248px;border-radius:6px;overflow:hidden;color:#fff}
.svc .title{position:absolute;left:20px;bottom:30px;font-size:29px;font-weight:500;line-height:37px}
.svc .title:after{content:"";display:block;width:140px;height:4px;background:var(--navy);margin-top:4px}
.svc.active{background:var(--navy);border:1px solid var(--navy)}
.svc.active .frame{position:absolute;inset:8px;border:2px solid #fff}
.svc.active .title{left:28px;top:12px;bottom:auto}
.svc.active .title:after{background:#fff}
.svc.active p{position:absolute;left:32px;top:108px;width:200px;font-size:14px;font-weight:300;line-height:23px}
.svc.active .mini{position:absolute;left:32px;top:194px;width:97px;height:19px;font-size:8px}

/* products */
.products{left:0;top:2355px;width:1193px;height:526px;background:linear-gradient(180deg,#1f4b8f,#1b4382)}
.products .section-h{color:#fff;top:82px;width:1200px}
.product{top:2516px;width:216px;height:260px;background:#fff;border-radius:16px;text-align:center}
.product .pic{width:112px;height:106px;margin:23px auto 0;border-radius:4px}
.product h4{font-size:15px;font-weight:600;margin-top:18px}
.product .price{font-size:21px;font-weight:600;color:var(--red);margin-top:6px}
.product .price s{color:#888;font-weight:500}
.product .buy{width:114px;height:30px;margin:10px auto 0;font-size:9px}

/* contact */
.form{left:65px;top:2961px;width:467px;height:490px;background:#f3f3f3;border:1px solid #e2e2e2}
.field{left:36px;width:392px;height:43px;background:#fff;border-radius:3px;font-size:13px;padding:14px 0 0 14px;color:#333}
.form-btn{left:85px;top:424px;width:301px;height:40px;font-size:12px}
.map{left:565px;top:2961px;width:570px;height:490px;background:linear-gradient(135deg,#dfe9d8,#eef1ea 45%,#b8d6ea 70%,#9cc6e4)}

/* footer */
.footer-bg{left:0;top:3500px}
.footer-logo{left:482px;top:3622px;width:272px;height:109px;background:#fff;display:flex;align-items:center;justify-content:center}
.fcol{top:3812px;color:#fff;width:250px}
.fcol h5{font-size:17px;font-weight:600;text-transform:uppercase}
.fcol h5:after{content:"";display:block;width:48px;height:3px;background:var(--blue);margin-top:12px}
.fcol .about-txt{font-size:13px;font-weight:300;line-height:26px;margin-top:34px;width:240px}
.fsocial{display:flex;gap:10px;margin-top:22px}
.fsocial span{width:38px;height:38px;border-radius:50%;background:var(--blue);display:block}
.crow{display:flex;gap:18px;margin-top:24px;font-size:13px;font-weight:300;line-height:20px}
.crow:first-of-type{margin-top:34px}
.crow b{font-weight:600;display:block}
.crow svg{flex:none;margin-top:10px}
.links{margin-top:30px}
.links div{display:flex;justify-content:space-between;font-size:12px;font-weight:300;padding:10px 0 10px;border-bottom:1px solid #2b3350}
.hours .crow b{font-weight:600}
</style>
</head>
<body>

<!-- header -->
<div class="abs topbar">
  <div class="item"><span class="dot"><svg width="10" height="8" viewBox="0 0 10 8"><rect x=".5" y=".5" width="9" height="7" fill="none" stroke="#fff"/><path d="M.5 .5L5 4.5 9.5 .5" fill="none" stroke="#fff"/></svg></span>hello@coastalbreezecool.com</div>
  <div class="item"><span class="dot"><svg width="10" height="10" viewBox="0 0 10 10"><path d="M2 1l2 2-1 1.5c.8 1.4 1.7 2.3 3 3L7.5 6l2 2-1.5 1.5C4.5 9 1 5.5.5 2z" fill="#fff"/></svg></span>555 010 2468</div>
  <div class="social"><span></span><span></span><span></span></div>
</div>
<div class="abs logo"><span class="mark"></span><div class="name">Coastal Breeze<br>Cooling Company</div></div>
<nav class="abs nav">
  <a style="left:0">HOME</a><a style="left:99px">ABOUT</a><a style="left:207px">SERVICES</a><a style="left:339px">PRODUCTS</a><a style="left:494px">FINANCING</a>
</nav>
<div class="abs btn quote-top">Get a Quote</div>

<!-- hero -->
<div class="abs" style="left:0;top:114px;width:1200px;height:1367px;background:var(--grey)"></div>
<svg class="abs hero-bg" width="1200" height="800" viewBox="0 114 1200 800" role="img" aria-label="Photo of a technician servicing a ceiling air conditioning unit">
  <defs><linearGradient id="heroShade" x1="0" y1="0" x2="1" y2="1"><stop offset="0" stop-color="#2b2b2e"/><stop offset=".5" stop-color="#3d3a38"/><stop offset="1" stop-color="#1e1f24"/></linearGradient></defs>
  <path d="M0 114H1200V600Q700 1130 0 705Z" fill="var(--red)"/>
  <path d="M0 114H1200V575Q700 1090 0 680Z" fill="url(#heroShade)"/>
</svg>
<h1 class="abs hero-title">Heating and<br>Air Conditioning<br>Services</h1>
<p class="abs hero-sub">Lorem ipsum dolor sit amet, consectetuer adipiscing elit.<br>Aenean commodo ligula eget dolor.</p>
<div class="abs btn hero-btn">Get a Quote</div>

<div class="abs feature" style="left:212px">
  <svg width="56" height="52" viewBox="0 0 56 52" fill="none" stroke="var(--navy)" stroke-width="2"><path d="M6 44V16h8v28M22 44V16h8v28M38 44V16h8v28M2 44h52"/><path d="M46 14c0-6 6-6 6-12" stroke="var(--red)"/></svg>
  <h3>Heating</h3><p>Lorem ipsum dolor sit amet,<br>consectetuer adipiscing elit.</p><div class="more">READ MORE</div>
</div>
<div class="abs feature" style="left:505px">
  <svg width="56" height="52" viewBox="0 0 56 52" fill="none" stroke="var(--navy)" stroke-width="2"><rect x="4" y="6" width="48" height="18" rx="3"/><path d="M10 18h36"/><circle cx="20" cy="36" r="10"/><path d="M20 26v20M11 31l18 10M11 41l18-10" stroke="var(--red)"/></svg>
  <h3>Cooling</h3><p>Lorem ipsum dolor sit amet,<br>consectetuer adipiscing elit.</p><div class="more">READ MORE</div>
</div>
<div class="abs feature" style="left:800px">
  <svg width="56" height="52" viewBox="0 0 56 52" fill="none" stroke="var(--navy)" stroke-width="2.5"><path d="M10 46L38 18M36 8a8 8 0 0 0 10 10l-6 2-4-4z"/><path d="M10 8l36 36M6 4l6 2 2 6" stroke="var(--red)"/></svg>
  <h3>Repairs</h3><p>Lorem ipsum dolor sit amet,<br>consectetuer adipiscing elit.</p><div class="more">READ MORE</div>
</div>

<!-- about -->
<div class="abs about-photo" role="img" aria-label="Photo of a technician in a blue cap working on an indoor AC unit"></div>
<div class="abs badge"><b>10+</b><span>Years of Experience</span></div>
<h2 class="abs about-h">ABOUT US</h2>
<div class="abs about-p">
  <p>Lorem ipsum dolor sit amet, consectetuer adipiscing elit. Aenean commodo ligula eget dolor. Aenean massa. Cum sociis natoque penatibus et magnis dis parturient montes, nascetur ridiculus mus.</p>
  <p>Lorem ipsum dolor sit amet, consectetuer adipiscing elit. Aenean commodo ligula eget dolor. Aenean massa. Cum sociis natoque penatibus et magnis dis parturient montes, nascetur ridiculus mus.</p>
</div>
<div class="abs btn about-btn">Read More</div>

<!-- services -->
<h2 class="abs section-h" style="top:1560px">What services we offer</h2>
<div class="abs svc" style="left:122px;top:1661px;background:linear-gradient(135deg,#6b5a4a,#3a5d8a 55%,#2c2a2a)" role="img" aria-label="Photo of a plumber fitting gas pipes"><div class="title">Gas<br>Fitting</div></div>
<div class="abs svc active" style="left:452px;top:1661px"><div class="frame"></div><div class="title">Pipe<br>Fitting</div><p>Nulla commodo dolor massa, vel pellentesque nulla congue quis.</p><div class="btn mini">Read More</div></div>
<div class="abs svc" style="left:807px;top:1661px;background:linear-gradient(135deg,#5c5f66,#9a9da3 55%,#3a3c40)" role="img" aria-label="Photo of a technician installing an outdoor AC unit"><div class="title">New<br>Installs</div></div>
<div class="abs svc" style="left:122px;top:1979px;background:linear-gradient(135deg,#8c7a62,#b6a58c 50%,#5b5a56)" role="img" aria-label="Photo of a technician servicing commercial equipment"><div class="title">Commercial<br>Services</div></div>
<div class="abs svc" style="left:452px;top:1979px;background:linear-gradient(135deg,#6f7f8f,#c0633a 45%,#3d5168)" role="img" aria-label="Photo of workers in hard hats on a building site"><div class="title">Building<br>Automations</div></div>
<div class="abs svc" style="left:807px;top:1979px;background:linear-gradient(180deg,#4a4c50,#7d8085 55%,#5a5c60)" role="img" aria-label="Photo of rooftop air conditioning units"><div class="title">Residential<br>Services</div></div>

<!-- products -->
<section class="abs products"><h2 class="abs section-h">Our best sellng products</h2></section>
<div class="abs product" style="left:73px"><div class="pic" role="img" aria-label="Blower fan motor" style="background:linear-gradient(135deg,#c9c4bc,#7c7770)"></div><h4>Product Title</h4><div class="price">$100 <s>$150</s></div><div class="btn buy">Buy Now</div></div>
<div class="abs product" style="left:348px"><div class="pic" role="img" aria-label="Capacitor with wiring" style="background:linear-gradient(135deg,#e9e9e9,#3a3a3a 60%,#c0602e)"></div><h4>Product Title</h4><div class="price">$100 <s>$150</s></div><div class="btn buy">Buy Now</div></div>
<div class="abs product" style="left:622px"><div class="pic" role="img" aria-label="Coiled sensor cable" style="background:linear-gradient(135deg,#f2f2f2,#a4a4a4)"></div><h4>Product Title</h4><div class="price">$100 <s>$150</s></div><div class="btn buy">Buy Now</div></div>
<div class="abs product" style="left:897px"><div class="pic" role="img" aria-label="Coiled sensor cable" style="background:linear-gradient(135deg,#f2f2f2,#a4a4a4)"></div><h4>Product Title</h4><div class="price">$100 <s>$150</s></div><div class="btn buy">Buy Now</div></div>

<!-- contact -->
<div class="abs form">
  <div class="abs field" style="top:40px">Name</div>
  <div class="abs field" style="top:98px">Email</div>
  <div class="abs field" style="top:153px">Phone</div>
  <div class="abs field" style="top:214px">Select Service</div>
  <div class="abs field" style="top:274px;height:126px;padding-top:20px">Message</div>
  <div class="abs btn form-btn">Request a Quote Now</div>
</div>
<div class="abs map" role="img" aria-label="Map of the Tampa area showing the service region"></div>

<!-- footer -->
<svg class="abs footer-bg" width="1200" height="705" viewBox="0 3500 1200 705">
  <path d="M0 3790Q600 3280 1200 3790V4205H0Z" fill="var(--red)"/>
  <path d="M6 3830Q600 3300 1200 3830V4205H6Z" fill="var(--ink)"/>
</svg>
<div class="abs footer-logo"><div class="logo" style="position:static"><span class="mark"></span><div class="name">Coastal Breeze<br>Cooling Company</div></div></div>

<div class="abs fcol" style="left:73px">
  <h5>About Us</h5>
  <p class="about-txt">We are an award winning plumbing company with over 20 years experience in the business. We provide a wide range of services for both residential and commercial clients.</p>
  <div class="fsocial"><span></span><span></span><span></span></div>
</div>
<div class="abs fcol" style="left:364px">
  <h5>Contact Us</h5>
  <div class="crow"><svg width="18" height="22" viewBox="0 0 18 22" fill="none" stroke="#8a90a6" stroke-width="1.5"><path d="M9 21s7-7 7-12A7 7 0 0 0 2 9c0 5 7 12 7 12z"/><circle cx="9" cy="9" r="2.5"/></svg><div><b>Address:</b>215 Bayview Road, Tampa, FL</div></div>
  <div class="crow"><svg width="18" height="18" viewBox="0 0 18 18" fill="none" stroke="#8a90a6" stroke-width="1.5"><path d="M3 1l4 4-2 2.5c1.5 2.8 3 4.3 5.5 5.5L13 11l4 4-3 3C7.5 17 1 10.5 0 4z"/></svg><div><b>Phone:</b>+1 555 010 3579</div></div>
  <div class="crow"><svg width="18" height="22" viewBox="0 0 18 22" fill="none" stroke="#8a90a6" stroke-width="1.5"><rect x="3" y="1" width="12" height="20" rx="2"/><path d="M7 17h4"/></svg><div><b>Mobile:</b>+1 555 010 4680</div></div>
  <div class="crow"><svg width="20" height="14" viewBox="0 0 20 14" fill="none" stroke="#8a90a6" stroke-width="1.5"><rect x="1" y="1" width="18" height="12"/><path d="M1 1l9 7 9-7"/></svg><div><b>Email:</b>support@coastalbreezecool.com</div></div>
</div>
<div class="abs fcol" style="left:656px;width:250px">
  <h5>Quick Links</h5>
  <div class="links">
    <div><span>About</span><span>›</span></div>
    <div><span>Contact</span><span>›</span></div>
    <div><span>News List</span><span>›</span></div>
    <div><span>Services</span><span>›</span></div>
    <div><span>Shop</span><span>›</span></div>
  </div>
</div>
<div class="abs fcol hours" style="left:947px">
  <h5>Opening Hours</h5>
  <div class="crow"><svg width="24" height="24" viewBox="0 0 24 24" fill="none" stroke="#8a90a6" stroke-width="1.5"><circle cx="12" cy="12" r="11"/><path d="M12 5v7h5"/></svg><div><b>Monday - Friday</b>8:00 AM - 5:00 PM</div></div>
  <div class="crow"><svg width="24" height="24" viewBox="0 0 24 24" fill="none" stroke="#8a90a6" stroke-width="1.5"><circle cx="12" cy="12" r="11"/><path d="M12 5v7h5"/></svg><div><b>Saturday</b>9:00 AM - 4:00 PM</div></div>
  <div class="crow"><svg width="24" height="24" viewBox="0 0 24 24" fill="none" stroke="#8a90a6" stroke-width="1.5"><circle cx="12" cy="12" r="11"/><path d="M12 5v7h5"/></svg><div><b>Sunday</b>CLOSED</div></div>
</div>

</body>
</html>
```